Redesign of business card for Cedar Ridge Mechanical

We are looking for a new design for our business cards for Cedar Ridge Mechanical. We are a plumbing & HVAC construction company, operating on the West Coast of Canada and USA. Logo attached.
Industry/Entity Type
Construction - Plumbing & HVAC
Contact Information for Business Card
Name, address, phone numbers, email, website address
Look and feel
Each slider illustrates characteristics of the customer's brand and the style your logo design should communicate.

```html
<!DOCTYPE html>
<html lang="en">
<head>
<meta charset="utf-8">
<title>Cedar Ridge Mechanical – Business Card</title>
<link href="https://fonts.googleapis.com/css2?family=Montserrat:wght@400;600;800&display=swap" rel="stylesheet">
<style>
  :root {
    --backdrop: #2e2e31;
    --card: #ffffff;
    --ink: #111111;
    --muted: #333333;
    --band: #000000;
    --band-text: #ffffff;
  }
  * { margin: 0; padding: 0; box-sizing: border-box; }
  html, body {
    width: 1200px; height: 913px; overflow: hidden;
    background: var(--backdrop);
    font-family: "Montserrat", Arial, sans-serif;
  }
  .canvas { position: relative; width: 1200px; height: 913px; }
  .card {
    position: absolute;
    width: 560px; height: 320px;
    background: var(--card);
    border-radius: 22px;
    overflow: hidden;
    box-shadow: 0 14px 30px rgba(0,0,0,.45);
  }
  .card--front { left: 70px; top: 90px; }
  .card--back { left: 570px; top: 500px; }

  .brand {
    display: flex; align-items: center; gap: 14px;
    color: var(--ink);
    font-weight: 800;
    text-transform: uppercase;
    line-height: 1.05;
  }
  .brand__mark { background: var(--ink); flex: none; }

  .card--front .brand {
    position: absolute; inset: 0;
    justify-content: center;
    font-size: 34px; letter-spacing: 1px;
  }
  .card--front .brand__mark { width: 30px; height: 30px; }

  .card--back .brand {
    position: absolute; left: 30px; top: 120px;
    width: 215px; font-size: 21px; gap: 10px;
  }
  .card--back .brand__mark { width: 18px; height: 18px; }

  .divider {
    position: absolute; left: 262px; top: 40px;
    width: 1.5px; height: 165px; background: var(--ink);
  }
  .contact {
    position: absolute; left: 284px; top: 38px;
    color: var(--muted); font-size: 15px; line-height: 1.35;
  }
  .contact__name { font-size: 25px; font-weight: 800; color: var(--ink); letter-spacing: .5px; }
  .contact__title { font-size: 15px; margin-bottom: 8px; }
  .contact__row { display: flex; align-items: center; gap: 7px; }
  .contact__row svg { width: 13px; height: 13px; flex: none; }
  .contact__address { margin-top: 8px; }

  .band { position: absolute; left: 0; bottom: 0; width: 560px; height: 110px; }
  .website {
    position: absolute; right: 70px; bottom: 22px;
    color: var(--band-text); font-size: 16px; letter-spacing: .3px;
  }
</style>
</head>
<body>
<main class="canvas">
  <section class="card card--front" aria-label="Card front">
    <div class="brand">
      <span class="brand__mark"></span>
      <span class="brand__name">Cedar Ridge Mechanical</span>
    </div>
  </section>

  <section class="card card--back" aria-label="Card back">
    <div class="brand">
      <span class="brand__mark"></span>
      <span class="brand__name">Cedar Ridge Mechanical</span>
    </div>
    <div class="divider"></div>
    <div class="contact">
      <div class="contact__name">DANIEL HART</div>
      <div class="contact__title">Managing Director</div>
      <div class="contact__row">
        <svg viewBox="0 0 24 24" fill="#111"><path d="M6.6 10.8a15 15 0 006.6 6.6l2.2-2.2a1 1 0 011-.25 11.4 11.4 0 003.6.6 1 1 0 011 1V20a1 1 0 01-1 1A17 17 0 013 4a1 1 0 011-1h3.5a1 1 0 011 1c0 1.25.2 2.45.6 3.6a1 1 0 01-.25 1z"/></svg>
        <span>123 456 789</span>
      </div>
      <div class="contact__row">
        <svg viewBox="0 0 24 24" fill="none" stroke="#111" stroke-width="2.4"><rect x="6" y="2" width="12" height="20" rx="2"/><line x1="10" y1="18" x2="14" y2="18"/></svg>
        <span>123 456 0000</span>
      </div>
      <div class="contact__row">
        <svg viewBox="0 0 24 24" fill="none" stroke="#111" stroke-width="2.4"><rect x="2" y="5" width="20" height="14" rx="2"/><path d="M2 6l10 7 10-7"/></svg>
        <span>info@yourgmail.com</span>
      </div>
      <div class="contact__address">Your address, City<br>State, Zip 1234</div>
    </div>
    <svg class="band" viewBox="0 0 560 110" aria-hidden="true">
      <path fill="#000" d="M230 110 L250 58 L262 52 L500 52 L520 38 L560 38 L560 110 Z"/>
    </svg>
    <div class="website">www.yourwebsite.com</div>
  </section>
</main>
</body>
</html>
```